Australian Trucking Company Requires Professional Looking Stationary

We require a professional looking stationary design that incorporates our newly designed logo.

Our business, called "Brell Haulage Contracting", provides contracting work, transport and logistics to business in Western Australia particularly with links to the mining sector.

We are a small business looking to expand and our new logo and our new stationary will help develop our brand image in our market place.

Target Market(s)

Businesses and Corporation with links to the Mining Sector

Industry/Entity Type

Small Business

Requirements
Must have
• The letterhead must have the following details:
The new logo

Text saying: "Brell Holdings Pty Ltd (ACN 582 316 907) ATF The Brell Discretionary Trust T/AS"
"ABN 71 834 209 553"
Address "P.O Box 817 Wattlegrove WA, 6958"
Phone: 08 9352 7140
Email: brellhaul@mailbox-example.com.au

The text on the letterhead should be editable as the details are likely to change in the near future. Provision should be made for a website address all though one isn't available at the moment.

The styling, layout and font text is entirely up to the designer.

```html
<!DOCTYPE html>
<html lang="en">
<head>
<meta charset="utf-8">
<title>Brell Haulage Contracting – Business Card</title>
<link href="https://fonts.googleapis.com/css2?family=Open+Sans:wght@400;600;700;800&display=swap" rel="stylesheet">
<style>
  :root{
    --bg:#e9e7e4;
    --card-white:#ffffff;
    --brand-red:#d7141f;
    --deep-red:#8e0a10;
    --darkest-red:#3a0306;
    --charcoal:#2a2a2a;
    --ink:#4d4d4d;
    --muted:#7a7a7a;
    --soft-grey:#ececec;
  }
  *{box-sizing:border-box;margin:0;padding:0}
  html,body{width:1200px;height:407px;overflow:hidden}
  body{background:var(--bg);font-family:"Open Sans",Arial,sans-serif;position:relative}

  .card{position:absolute;top:60px;height:288px;box-shadow:0 4px 10px rgba(0,0,0,.35)}

  /* Front */
  .card-front{left:58px;width:521px;background:var(--card-white);overflow:hidden}
  .brand-square{position:absolute;left:0;top:0;width:91px;height:85px;
    background:linear-gradient(160deg,#3a3a3a,var(--charcoal) 60%,#1a1a1a)}
  .brand-name{position:absolute;left:100px;top:24px;color:var(--brand-red);
    font-weight:800;font-size:17px;line-height:17px;text-transform:uppercase;letter-spacing:.2px}
  .divider-line{position:absolute;left:0;top:88px;width:150px;height:2px;background:var(--brand-red)}
  .accent-band{position:absolute;left:0;top:92px;width:69px;height:196px;
    background:linear-gradient(180deg,var(--brand-red) 0%,#b10e17 45%,var(--darkest-red) 100%)}
  .accent-rule{position:absolute;left:72px;top:92px;width:3px;height:196px;
    background:linear-gradient(180deg,var(--brand-red),var(--darkest-red))}
  .entity-details{position:absolute;left:94px;top:95px;font-size:10.5px;color:var(--ink);line-height:21px}

  .contact-list{position:absolute;left:80px;top:206px;list-style:none;font-size:10.5px;color:var(--ink)}
  .contact-list li{display:flex;align-items:center;height:17px}
  .contact-list li.address{margin-bottom:6px}
  .contact-list svg{width:9px;height:9px;margin-right:5px;fill:var(--charcoal);flex:none}

  .faint-mark{position:absolute;left:345px;top:125px;width:150px;height:130px;
    background:radial-gradient(ellipse at center,var(--soft-grey) 0%,rgba(236,236,236,0) 70%)}

  .holder{position:absolute;right:14px;top:262px;color:var(--brand-red);font-size:16px;font-weight:700}
  .holder .title{color:var(--muted);font-size:10.5px;font-weight:400}

  /* Back */
  .card-back{left:639px;width:503px;
    background:radial-gradient(ellipse 60% 70% at 50% 42%,#e02a31 0%,#b5121a 45%,var(--deep-red) 100%)}
  .back-name{position:absolute;left:0;right:0;top:100px;text-align:center;color:#f3b8bb;
    font-weight:800;font-size:26px;line-height:30px;text-transform:uppercase}
  .back-web{position:absolute;left:0;right:0;top:266px;text-align:center;color:#fff;
    font-weight:700;font-size:13px;letter-spacing:2.6px}
</style>
</head>
<body>
  <section class="card card-front" aria-label="Business card front">
    <div class="brand-square"></div>
    <div class="brand-name">Brell<br>Haulage<br>Contracting</div>
    <div class="divider-line"></div>
    <div class="accent-band"></div>
    <div class="accent-rule"></div>

    <div class="entity-details">
      <p>Brell Holdings Pty Ltd (ACN 582 316 907) ATF The Brell Discretionary Trust T/AS</p>
      <p>ABN 71 834 209 553</p>
    </div>

    <div class="faint-mark" role="img" aria-label="Faint brand mark area"></div>

    <ul class="contact-list">
      <li class="address">
        <svg viewBox="0 0 10 10"><path d="M5 0.5 0 5h1.5v4.5h2.7V6.6h1.6v2.9h2.7V5H10z"/></svg>
        P.O Box 817 Wattlegrove WA, 6958
      </li>
      <li>
        <svg viewBox="0 0 10 10"><circle cx="5" cy="5" r="4.5" fill="none" stroke="#2a2a2a" stroke-width="1"/><path d="M3.2 2.5c.4-.3.8 0 1 .5l.3.7c.1.3-.2.5-.4.7.3.7.8 1.2 1.5 1.5.2-.2.4-.5.7-.4l.7.3c.5.2.8.6.5 1-.6.8-1.6.8-2.6.1C3.8 6.2 3 5.1 2.8 4c-.1-.6 0-1.1.4-1.5z"/></svg>
        08 9352 7140
      </li>
      <li>
        <svg viewBox="0 0 10 10"><path d="M0.5 2h9v6h-9z" /><path d="M0.8 2.3 5 5.6l4.2-3.3" fill="none" stroke="#fff" stroke-width=".8"/></svg>
        brellhaul@mailbox-example.com.au
      </li>
      <li>
        <svg viewBox="0 0 10 10"><circle cx="5" cy="5" r="4.5"/><path d="M0.5 5h9M5 .5c-2 2.5-2 6.5 0 9M5 .5c2 2.5 2 6.5 0 9" fill="none" stroke="#fff" stroke-width=".6"/></svg>
        www.brellhaul-example.com.au
      </li>
    </ul>

    <p class="holder">Your Name <span class="title">/ Title</span></p>
  </section>

  <section class="card card-back" aria-label="Business card back">
    <div class="back-name">Brell Haulage<br>Contracting</div>
    <p class="back-web">www.brellhaul-example.com.au</p>
  </section>
</body>
</html>
```